Redesign of Form/Document Navigation Page

I need a redesign of our document and navigation bar on the left. We want the same navigation bar layout/setup but want the buttons and typography to be simple and matching all over. The form needs to be aesthetically pleasing and fit within the page.

1st attachment is our Direct Deposit and the second is the form continued.

```html
<!DOCTYPE html>
<html lang="en">
<head>
<meta charset="utf-8">
<title>Sentinel Patrol Services – Direct Deposit</title>
<link rel="stylesheet" href="https://fonts.googleapis.com/css2?family=Arimo:wght@400;700&family=Roboto+Slab:wght@400;700&display=swap">
<style>
  :root{
    --navy:#1c3f94;
    --orange:#f2a51c;
    --text:#6f6f6f;
    --label:#555;
    --line:#d9dde3;
    --page:#f5f6f8;
    --white:#ffffff;
  }
  *{box-sizing:border-box;margin:0;padding:0}
  html,body{width:1200px;height:1013px;overflow:hidden}
  body{background:var(--page);font-family:"Arimo",Arial,sans-serif;color:var(--text);position:relative}

  .site-header{position:absolute;left:0;top:0;width:1200px;height:88px;background:var(--white);box-shadow:0 1px 4px rgba(0,0,0,.08)}
  .brand{position:absolute;left:25px;top:20px;display:flex;align-items:center;gap:10px}
  .brand-mark{width:44px;height:44px;border-radius:50%;background:var(--navy)}
  .brand-name{font-family:"Arimo",Arial,sans-serif;font-weight:700;font-size:19px;line-height:20px;color:var(--orange);text-transform:uppercase;width:170px}
  .top-nav{position:absolute;right:29px;top:35px;display:flex;align-items:center;font-size:12px;color:#666}
  .top-nav a{color:#666;text-decoration:none}
  .top-nav .sep{margin:0 28px}
  .power-btn{margin-left:13px;width:28px;height:23px;background:var(--navy);display:flex;align-items:center;justify-content:center}

  .back-tab{position:absolute;left:25px;top:115px;width:119px;height:31px;background:var(--navy);color:#fff;font-size:11.5px;font-weight:700;display:flex;align-items:center;justify-content:center}
  .side-nav{position:absolute;left:25px;top:146px;width:246px;height:643px;background:var(--white);border:1px solid #e6e8ec}
  .side-item{height:91px;border-bottom:1px solid #e6e8ec;display:flex;align-items:center;padding-left:16px;gap:14px;font-size:11.5px;font-weight:700;color:#555}
  .side-item:last-child{border-bottom:none}
  .side-icon{width:54px;height:54px;flex:none}

  .panel{position:absolute;left:285px;top:147px;width:886px;height:767px;background:var(--white);border:1px solid #e3e6ea;overflow:hidden}
  .scrollbar{position:absolute;right:0;top:0;width:13px;height:100%;background:#f1f1f1;border-left:1px solid #e5e5e5}
  .scroll-thumb{position:absolute;left:2px;top:74px;width:9px;height:316px;background:#c9c9c9;border-radius:2px}
  .panel > *{position:absolute;left:22px}

  .form-title{top:19px;font-family:"Roboto Slab",serif;font-size:17px;color:var(--orange)}
  .intro{top:58px;width:826px;font-size:11px;line-height:20.2px}
  .attach{top:162px;width:670px;height:45px;border:1px solid var(--line);background:#f6f7f8;font-size:11px;display:flex;align-items:center;padding-left:16px}
  .refresh-btn{top:162px;left:700px!important;width:145px;height:45px;background:var(--navy);color:#fff;font-size:14.5px;font-weight:700;border-radius:3px;display:flex;align-items:center;justify-content:center}
  .section-title{top:229px;font-family:"Roboto Slab",serif;font-size:17px;color:var(--navy)}
  .note{top:267px;font-size:11px}
  .prompt{top:295px;font-family:"Roboto Slab",serif;font-size:13.5px;color:#555}
  .notice{top:326px;font-family:"Roboto Slab",serif;font-size:11px;color:var(--orange)}
  .choice-row{display:flex;gap:32px;font-size:11.5px;color:#555}
  .choice{display:flex;align-items:center;gap:8px}
  .box{width:14px;height:14px;border:1px solid #ccc;border-radius:3px;background:#f4f4f4}
  .enroll-row{top:359px}
  .field{width:255px}
  .field label{display:block;font-size:11.5px;color:#666;margin-bottom:7px}
  .field .input{height:33px;border:1px solid #cfd3d8;border-radius:2px}
  .account-row{top:566px}
  .amount{top:564px;left:449px!important;font-size:14.5px;font-weight:700;color:var(--orange)}
  .important{top:627px;font-family:"Roboto Slab",serif;font-size:17px;color:var(--orange)}
  .important strong{font-weight:700}
  .terms{top:668px;width:826px;font-size:11px;line-height:20.2px}

  .site-footer{position:absolute;left:0;top:952px;width:1200px;height:61px;background:var(--navy);color:#fff;font-size:11px}
  .copyright{position:absolute;left:25px;top:24px}
  .social{position:absolute;right:59px;top:14px;display:flex;gap:6px}
  .social span{width:32px;height:32px;border:1.5px solid #fff;border-radius:50%}
  .page-code{position:absolute;right:6px;top:44px;font-size:10px}
</style>
</head>
<body>
<header class="site-header">
  <div class="brand"><span class="brand-mark"></span><span class="brand-name">Sentinel Patrol Services</span></div>
  <nav class="top-nav">
    <a href="#">HOME</a><span class="sep">|</span><a href="#">HELP</a>
    <span class="power-btn"><svg width="12" height="12" viewBox="0 0 12 12" fill="none" stroke="#fff" stroke-width="1.6" stroke-linecap="round"><path d="M3.5 3a4 4 0 1 0 5 0"/><path d="M6 1v4.5"/></svg></span>
  </nav>
</header>

<div class="back-tab">BACK TO PROFILE</div>
<nav class="side-nav">
  <div class="side-item"><svg class="side-icon" viewBox="0 0 54 54"><circle cx="27" cy="27" r="25.5" fill="none" stroke="#1c3f94" stroke-width="2"/><rect x="15" y="20" width="24" height="14" rx="1" fill="none" stroke="#1c3f94" stroke-width="2"/><circle cx="27" cy="27" r="3.5" fill="none" stroke="#1c3f94" stroke-width="2"/></svg>DIRECT DEPOSIT</div>
  <div class="side-item"><svg class="side-icon" viewBox="0 0 54 54"><circle cx="27" cy="27" r="25.5" fill="none" stroke="#f2a51c" stroke-width="2"/><path d="M16 27a11 11 0 0 1 19-7.5M38 27a11 11 0 0 1-19 7.5" fill="none" stroke="#f2a51c" stroke-width="2.4"/><circle cx="27" cy="25" r="4" fill="#f2a51c"/></svg>CHANGE W-4</div>
  <div class="side-item"><svg class="side-icon" viewBox="0 0 54 54"><circle cx="27" cy="27" r="25.5" fill="none" stroke="#1c3f94" stroke-width="2"/><rect x="18" y="15" width="17" height="23" fill="none" stroke="#1c3f94" stroke-width="2"/><path d="M21 21h11M21 25h11M21 29h8" stroke="#1c3f94" stroke-width="1.6"/></svg>LABOUR CODE</div>
  <div class="side-item"><svg class="side-icon" viewBox="0 0 54 54"><circle cx="27" cy="27" r="25.5" fill="none" stroke="#f2a51c" stroke-width="2"/><circle cx="25" cy="20" r="5.5" fill="#f2a51c"/><path d="M14 38a11 9 0 0 1 19-5v5z" fill="#f2a51c"/><circle cx="35" cy="35" r="5.5" fill="#fff" stroke="#f2a51c" stroke-width="2"/><path d="M35 32v6M32 35h6" stroke="#f2a51c" stroke-width="1.6"/></svg>PERSONAL INFO</div>
  <div class="side-item"><svg class="side-icon" viewBox="0 0 54 54"><circle cx="27" cy="27" r="25.5" fill="none" stroke="#1c3f94" stroke-width="2"/><path d="M16 19h4M16 27h4M16 35h4M24 19h14M24 27h14M24 35h14" stroke="#1c3f94" stroke-width="2"/></svg>APPRAISEL &amp; REVIEW</div>
  <div class="side-item"><svg class="side-icon" viewBox="0 0 54 54"><circle cx="27" cy="27" r="25.5" fill="none" stroke="#f2a51c" stroke-width="2"/><rect x="19" y="17" width="17" height="20" fill="none" stroke="#f2a51c" stroke-width="2"/><path d="M22 22h11M22 26h11M22 30h7" stroke="#f2a51c" stroke-width="1.6"/></svg>WRITE UP-SLIP</div>
  <div class="side-item"><svg class="side-icon" viewBox="0 0 54 54"><circle cx="27" cy="27" r="25.5" fill="none" stroke="#1c3f94" stroke-width="2"/><path d="M17 38v-6M23 38v-10M29 38v-8M35 38v-14" stroke="#1c3f94" stroke-width="4"/><path d="M16 30l8-8 5 4 9-9" fill="none" stroke="#1c3f94" stroke-width="2"/></svg>EMPLOYEE PERFORMANCE</div>
</nav>

<main class="panel">
  <h1 class="form-title">Employee Direct Deposit Enrollment Form</h1>
  <p class="intro">To enroll in Direct Deposit, simply fill out this form. Attach a voided check for each checking account - not a deposit slip. If depositing to a savings account, ask your bank to give you the Routing/Transit Number for your account. It isn't always the same as the number on a savings deposit slip. This will help ensure that you are paid correctly. Once filled out, accounting will review your information for processing. Once processed, you will receive an email confirmation with details. Employees must attach a voided check for each of their accounts to help verify their account numbers and bank routing numbers.</p>
  <div class="attach">Attach A Voided Check Or Bank Deposit Form for the Account</div>
  <div class="refresh-btn">REFRESH</div>
  <h2 class="section-title">Account Information</h2>
  <p class="note">The last item must be for the remaining amount owed to you. To distribute to more accounts, please complete another form.</p>
  <p class="prompt">Make sure to indicate what kind of account, along with enrolling or declining</p>
  <p class="notice">**NOTIFY PAYROLL IMMEDIATELY IF YOU CLOSE OR CHANGE BANK ACCOUNT**</p>
  <div class="choice-row enroll-row">
    <span class="choice"><span class="box"></span>New Enrollment</span>
    <span class="choice"><span class="box"></span>Change Enrollment</span>
    <span class="choice"><span class="box"></span>Cancel Enrollment</span>
  </div>
  <div class="field" style="top:420px"><label>Bank Name:</label><div class="input"></div></div>
  <div class="field" style="top:420px;left:301px"><label>City:</label><div class="input"></div></div>
  <div class="field" style="top:420px;left:579px"><label>State:</label><div class="input"></div></div>
  <div class="field" style="top:491px"><label>Routing Transit #:</label><div class="input"></div></div>
  <div class="field" style="top:491px;left:301px"><label>Account Number:</label><div class="input"></div></div>
  <div class="choice-row account-row" style="gap:60px">
    <span class="choice"><span class="box"></span>Checking</span>
    <span class="choice"><span class="box"></span>Savings</span>
  </div>
  <div class="amount">Amount: 100%</div>
  <h2 class="important"><strong>IMPORTANT!</strong> Please read and sign before completing and submitting</h2>
  <p class="terms">I hereby authorize SENTINEL PATROL SERVICES to deposit any amounts owed me, as instructed by my employer, by initiating credit entries to my account at the financial institution (hereinafter "Bank") indicated on this form. Further, I authorize Bank to accept and to credit any credit entries indicated by SENTINEL PATROL SERVICES to my account. In the event that SENTINEL PATROL SERVICES deposits funds erroneously into my account, I authorize SENTINEL PATROL SERVICES to</p>
  <div class="scrollbar" style="left:auto"><div class="scroll-thumb"></div></div>
</main>

<footer class="site-footer">
  <span class="copyright">Copyright © 2016 SPS.All Rights Reserved.</span>
  <div class="social"><span></span><span></span><span></span><span></span><span></span></div>
  <span class="page-code">C2</span>
</footer>
</body>
</html>
```